Banner für Immobilienmakler
Zielgruppe
Immobilienmakler, Immobilienverkauf mit Herz,
Aufgabenstellung
Verkauf von Häusern und Wohnungen, der Banner soll an einen Balkon oder einen Zaun angebracht werden mit dem Hinweis, dass das Haus Zu verkaufen ist.
Maße ca. 76 x 244cm
Es darf gerne frech und modern sein mit einem witzigen einladenden Spruch sein, sollte aber auch ansonsten zu meinem chicen Style passen (siehe Homepage www.karwendimmobilien.de) es soll sich abheben von anderen langweiligen Bannern.
Ggf soll die Plane auch noch an einem Tennisplatz angebracht werden

```html
<!DOCTYPE html>
<html lang="de">
<head>
<meta charset="utf-8">
<title>Banner – Karwend Immobilien</title>
<link href="https://fonts.googleapis.com/css2?family=Roboto:wght@400;500;700;900&display=swap" rel="stylesheet">
<style>
  :root {
    --page-bg: #e6e6e6;
    --stone-dark: #2a2a2a;
    --stone-dark-2: #3a3a3a;
    --sand: #dcc7a3;
    --sand-2: #cdb48a;
    --gold: #c9a567;
    --ink: #1c1c1c;
    --white: #ffffff;
  }
  * { margin: 0; padding: 0; box-sizing: border-box; }
  html, body {
    width: 1200px; height: 720px; overflow: hidden;
    background: var(--page-bg);
    font-family: "Roboto", Arial, sans-serif;
  }
  .banner {
    position: absolute; left: 20px; top: 166px;
    width: 1160px; height: 388px;
    background: linear-gradient(135deg, var(--stone-dark-2), var(--stone-dark));
    overflow: hidden;
  }
  .banner-shapes { position: absolute; inset: 0; }
  .brand-name {
    position: absolute; left: 40px; top: 80px; width: 260px;
    color: var(--gold); font-weight: 700; font-size: 40px; line-height: 1.1;
    text-align: center; letter-spacing: 0.5px;
  }
  .headline-intro {
    position: absolute; left: 494px; top: 52px;
    font-size: 56px; font-weight: 400; color: var(--ink); letter-spacing: -0.5px;
  }
  .headline-main {
    position: absolute; left: 540px; top: 118px;
    font-size: 60px; font-weight: 900; color: var(--ink); letter-spacing: -1px;
  }
  .sale-strip {
    position: absolute; left: 398px; top: 200px;
    font-size: 35px; font-weight: 500; color: var(--white); white-space: nowrap;
  }
  .sale-strip strong { color: var(--gold); font-weight: 700; }
  .contact-row {
    position: absolute; left: 30px; top: 322px; height: 40px;
    display: flex; align-items: center; color: var(--white);
  }
  .contact-item { position: absolute; display: flex; align-items: center; gap: 10px; white-space: nowrap; }
  .contact-phone { left: 0; font-size: 28px; font-weight: 700; }
  .contact-mail { left: 346px; font-size: 21px; font-weight: 500; }
  .contact-web { left: 688px; font-size: 21px; font-weight: 500; }
  .contact-item svg { flex: none; }
</style>
</head>
<body>
  <div class="banner">
    <svg class="banner-shapes" width="1160" height="388" viewBox="0 0 1160 388">
      <defs>
        <linearGradient id="sandFill" x1="0" y1="0" x2="1" y2="1">
          <stop offset="0" stop-color="#d9c29c"/>
          <stop offset="0.5" stop-color="#e2cfae"/>
          <stop offset="1" stop-color="#d2ba90"/>
        </linearGradient>
      </defs>
      <polygon points="459,7 1160,7 1160,311 292,311" fill="url(#sandFill)"/>
      <polygon points="364,247 393,196 1140,196 1140,247" fill="var(--stone-dark)"/>
      <circle cx="1081" cy="310" r="44" fill="var(--stone-dark)" stroke="var(--gold)" stroke-width="1.5"/>
    </svg>

    <div class="brand-name">Karwend<br>Immobilien</div>

    <div class="headline-intro">Lust auf einen</div>
    <div class="headline-main">TAPETENWECHSEL?</div>
    <div class="sale-strip">DIESE IMMOBILIE STEHT <strong>ZUM VERKAUF!</strong></div>

    <div class="contact-row">
      <div class="contact-item contact-phone">
        <svg width="26" height="26" viewBox="0 0 24 24"><path fill="var(--gold)" d="M6.6 10.8a15.2 15.2 0 0 0 6.6 6.6l2.2-2.2c.3-.3.7-.4 1-.2 1.1.4 2.3.6 3.6.6.6 0 1 .4 1 1V20c0 .6-.4 1-1 1A17 17 0 0 1 3 4c0-.6.4-1 1-1h3.5c.6 0 1 .4 1 1 0 1.3.2 2.5.6 3.6.1.3 0 .7-.2 1z"/></svg>
        <span>04321 / 55 60 718</span>
      </div>
      <div class="contact-item contact-mail">
        <svg width="26" height="18" viewBox="0 0 26 18"><rect x="1" y="1" width="24" height="16" fill="var(--gold)"/><path d="M1 1l12 9 12-9" fill="none" stroke="var(--stone-dark)" stroke-width="1.6"/></svg>
        <span>info@karwendimmobilien.de</span>
      </div>
      <div class="contact-item contact-web">
        <svg width="26" height="26" viewBox="0 0 26 26" fill="none" stroke="var(--gold)" stroke-width="1.6"><circle cx="13" cy="13" r="11"/><ellipse cx="13" cy="13" rx="5" ry="11"/><path d="M2 13h22M4 7h18M4 19h18"/></svg>
        <span>www.karwendimmobilien.de</span>
      </div>
    </div>
  </div>
</body>
</html>
```